Design concept Visual UI of future mobile app - healthcare

Hi,
I'm looking for a top designer, innovative with strong experience in user interface

The app will be connected to a future health website related to depression and addiction by helping the user to track the moods, tired, anxiety using this mobile app.

I attached the deck of the overall project but I can send you a specific presentation for the app only

thanks

Target Market(s)

Switzerland, UK, Germany and France

Industry/Entity Type

Mental Health

Logo Text

Health, hope

Font styles to use
Sans Serif

Colors
cee9f5
33a6d7
0692cd
0255a3
3276b5
85abd2

Requirements
Must have
• keep it simple, easy to navigate
• The user should be able to track the moods on a daily basis,
• sleep time, and rate how the feel on the day
• To be able to get information from the sync deck of vexlo
Nice to have
• to be able share this app with a friend

```html
<!DOCTYPE html>
<html lang="en">
<head>
<meta charset="utf-8">
<title>Mood Tracker – App Screens</title>
<link rel="stylesheet" href="https://fonts.googleapis.com/css2?family=Roboto:wght@400;500;700&display=swap">
<style>
  :root {
    --sky-pale: #cee9f5;
    --sky: #33a6d7;
    --ocean: #0692cd;
    --navy: #0255a3;
    --steel: #3276b5;
    --mist: #85abd2;
    --stage: #efefef;
    --screen-top: #f4f4f4;
    --screen-bottom: #e1e1e1;
    --bar: #111;
    --white: #fff;
  }
  * { box-sizing: border-box; margin: 0; padding: 0; }
  html, body { width: 1200px; height: 800px; overflow: hidden; }
  body {
    background: var(--stage);
    font-family: "Roboto", Arial, sans-serif;
    font-weight: 400;
    position: relative;
    color: var(--steel);
  }
  .screen {
    position: absolute;
    top: 228px;
    width: 190px;
    height: 336px;
    border: 2px solid #1c1c1c;
    background: linear-gradient(var(--screen-top), var(--screen-bottom));
    overflow: hidden;
  }
  .screen--graphs { left: 231px; }
  .screen--profile { left: 508px; }
  .screen--activity { left: 784px; }

  .status-bar {
    height: 12px;
    background: var(--bar);
    color: var(--white);
    font-size: 5.5px;
    display: flex;
    align-items: center;
    justify-content: space-between;
    padding: 0 5px;
  }
  .status-bar__time { font-weight: 500; }
  .status-bar__battery { display: flex; align-items: center; gap: 2px; }
  .battery { width: 11px; height: 5px; border: 1px solid var(--white); background: var(--white); }

  .app-header {
    height: 30px;
    background: var(--sky-pale);
    position: relative;
  }
  .app-header__title {
    position: absolute;
    left: 52px;
    right: 26px;
    top: 0;
    height: 30px;
    line-height: 30px;
    text-align: center;
    white-space: nowrap;
    font-size: 8px;
    font-weight: 400;
    letter-spacing: 0.2px;
    color: var(--steel);
    text-transform: uppercase;
  }
  .app-header__title--bold { font-weight: 700; }
  .app-header__menu { position: absolute; left: 18px; top: 9px; }
  .app-header__prev { position: absolute; left: 42px; top: 10px; }
  .app-header__next { position: absolute; right: 18px; top: 10px; }

  .chart-title {
    position: absolute;
    width: 100%;
    text-align: center;
    font-size: 6.5px;
    font-weight: 700;
    color: var(--steel);
  }
  .chart { position: absolute; }
  .chart-months {
    position: absolute;
    display: flex;
    justify-content: space-between;
    font-size: 3.6px;
    color: #666;
  }
  .chart-years {
    position: absolute;
    left: 20px;
    top: 238px;
    font-size: 4px;
    color: #555;
    line-height: 9px;
  }

  .profile-name {
    position: absolute; top: 46px; width: 100%;
    text-align: center; font-size: 8.5px; font-weight: 700; color: var(--steel);
  }
  .profile-photo {
    position: absolute; left: 39px; top: 63px; width: 45px; height: 50px;
    border: 2px solid var(--white);
    background: linear-gradient(160deg, #b88a5a, #e3c3a4 55%, #cfd3d6);
  }
  .profile-facts {
    position: absolute; left: 94px; top: 64px;
    font-size: 8.5px; line-height: 13px; color: var(--steel);
  }
  .profile-facts b { color: var(--navy); font-weight: 700; }
  .action-button {
    position: absolute; left: 25px; width: 94px; height: 14px;
    background: linear-gradient(var(--ocean), var(--navy));
    color: var(--white); font-size: 6.3px;
    display: flex; align-items: center; padding-left: 6px; gap: 4px;
    border-radius: 1px;
  }
  .action-button__more {
    position: absolute; right: 3px; top: 3px;
    background: var(--white); color: var(--steel);
    font-size: 3.6px; padding: 1.5px 2px; border-radius: 1px;
  }
  .section-title {
    position: absolute; left: 18px; font-size: 8px; color: var(--ocean); white-space: nowrap;
  }
  .add-profile {
    position: absolute; left: 98px; top: 184px;
    font-size: 5.5px; color: #333; display: flex; align-items: center; gap: 2px;
  }
  .list-card {
    position: absolute; left: 26px; width: 112px;
    background: #f4f4f4; box-shadow: 0 1px 2px rgba(0,0,0,.18);
  }
  .list-card__row {
    height: 20px; display: flex; align-items: center; justify-content: space-between;
    padding: 0 5px; font-size: 5.5px; font-weight: 700; color: #777;
    border-bottom: 1px solid #e0e0e0;
  }
  .list-card__row:last-child { border-bottom: none; }
  .list-card__count { font-weight: 400; color: #aaa; }
  .chevron { color: var(--ocean); font-weight: 700; font-size: 7px; }

  .activity-feed { position: absolute; left: 17px; top: 61px; width: 160px; }
  .activity-item__title { font-size: 8.5px; font-weight: 400; color: var(--ocean); line-height: 11px; }
  .activity-item__body { font-size: 6.2px; line-height: 11px; color: var(--steel); }
  .activity-item__list { list-style: none; }
  .activity-item__list li { text-indent: 5px; }
  .activity-item__date { font-size: 6px; line-height: 10px; color: #666; margin-bottom: 2px; }
</style>
</head>
<body>

<section class="screen screen--graphs">
  <div class="status-bar">
    <span>●●●○○ NOVA</span><span class="status-bar__time">4:21 PM</span>
    <span class="status-bar__battery">100% <span class="battery"></span></span>
  </div>
  <header class="app-header">
    <svg class="app-header__menu" width="12" height="11" viewBox="0 0 12 11"><rect y="0" width="12" height="2.4" fill="#3276b5"/><rect y="4.3" width="12" height="2.4" fill="#3276b5"/><rect y="8.6" width="12" height="2.4" fill="#3276b5"/></svg>
    <svg class="app-header__prev" width="5" height="8" viewBox="0 0 5 8"><path d="M4 0.5 0.8 4 4 7.5" fill="none" stroke="#fff" stroke-width="1.2"/></svg>
    <span class="app-header__title">Tracking graphs</span>
    <svg class="app-header__next" width="5" height="8" viewBox="0 0 5 8"><path d="M1 0.5 4.2 4 1 7.5" fill="none" stroke="#fff" stroke-width="1.2"/></svg>
  </header>

  <div class="chart-title" style="top:52px">MONTH 2015</div>
  <svg class="chart" style="left:26px;top:65px" width="138" height="98" viewBox="0 0 138 98">
    <defs>
      <linearGradient id="mood-scale" x1="0" y1="0" x2="0" y2="1">
        <stop offset="0" stop-color="#e8402a"/>
        <stop offset="0.3" stop-color="#f0971f"/>
        <stop offset="0.48" stop-color="#c9b233"/>
        <stop offset="0.62" stop-color="#8c9a3c"/>
        <stop offset="1" stop-color="#5e7a3c"/>
      </linearGradient>
    </defs>
    <rect width="138" height="98" fill="url(#mood-scale)"/>
    <g stroke="#fff" stroke-opacity=".25" stroke-width=".5">
      <line x1="11.5" y1="0" x2="11.5" y2="98"/><line x1="23" y1="0" x2="23" y2="98"/><line x1="34.5" y1="0" x2="34.5" y2="98"/><line x1="46" y1="0" x2="46" y2="98"/><line x1="57.5" y1="0" x2="57.5" y2="98"/><line x1="69" y1="0" x2="69" y2="98"/><line x1="80.5" y1="0" x2="80.5" y2="98"/><line x1="92" y1="0" x2="92" y2="98"/><line x1="103.5" y1="0" x2="103.5" y2="98"/><line x1="115" y1="0" x2="115" y2="98"/><line x1="126.5" y1="0" x2="126.5" y2="98"/>
    </g>
    <line x1="0" y1="50" x2="138" y2="50" stroke="#fff" stroke-opacity=".7" stroke-width=".6"/>
    <path d="M0 40 C8 38 12 34 18 36 S28 26 34 30 S44 44 50 40 S58 30 64 34 S74 48 80 44 S88 28 94 36 S104 58 110 54 S114 28 118 30 S126 42 132 40 L138 38" fill="none" stroke="#fff" stroke-width=".9"/>
  </svg>
  <div class="chart-months" style="left:28px;top:168px;width:134px">
    <span>Jan</span><span>Feb</span><span>Mar</span><span>Apr</span><span>May</span><span>Jun</span><span>Jul</span><span>Aug</span><span>Sep</span><span>Oct</span><span>Nov</span><span>Dec</span>
  </div>

  <div class="chart-title" style="top:190px">YEAR</div>
  <div class="chart-years"><div>2016</div><div>2015</div><div>2014</div></div>
  <svg class="chart" style="left:34px;top:202px" width="137" height="98" viewBox="0 0 137 98">
    <rect width="137" height="98" fill="url(#mood-scale)"/>
    <g stroke="#fff" stroke-opacity=".25" stroke-width=".5">
      <line x1="11.4" y1="0" x2="11.4" y2="98"/><line x1="22.8" y1="0" x2="22.8" y2="98"/><line x1="34.2" y1="0" x2="34.2" y2="98"/><line x1="45.6" y1="0" x2="45.6" y2="98"/><line x1="57" y1="0" x2="57" y2="98"/><line x1="68.4" y1="0" x2="68.4" y2="98"/><line x1="79.8" y1="0" x2="79.8" y2="98"/><line x1="91.2" y1="0" x2="91.2" y2="98"/><line x1="102.6" y1="0" x2="102.6" y2="98"/><line x1="114" y1="0" x2="114" y2="98"/><line x1="125.4" y1="0" x2="125.4" y2="98"/>
    </g>
    <g stroke="#fff" stroke-opacity=".6" stroke-width=".5">
      <line x1="0" y1="38" x2="137" y2="38"/><line x1="0" y1="47" x2="137" y2="47"/><line x1="0" y1="56" x2="137" y2="56"/>
    </g>
    <path d="M0 36 C8 40 14 30 22 34 S32 42 40 36 S52 26 58 30 S66 44 74 40 S86 32 92 36 S100 44 108 38 S120 34 128 40 L137 38" fill="none" stroke="#fff" stroke-width=".8"/>
    <path d="M0 52 C6 46 12 44 18 48 S28 60 36 54 S46 40 54 46 S62 58 70 52 S80 44 88 48 S98 60 106 56 S118 46 124 52 L137 50" fill="none" stroke="#fff" stroke-opacity=".85" stroke-width=".7"/>
    <path d="M0 60 C8 56 14 64 22 60 S34 50 42 56 S52 68 60 62 S72 54 80 60 S92 70 100 64 S110 52 118 60 S128 70 137 66" fill="none" stroke="#fff" stroke-opacity=".7" stroke-width=".7"/>
  </svg>
  <div class="chart-months" style="left:36px;top:304px;width:133px">
    <span>Jan</span><span>Feb</span><span>Mar</span><span>Apr</span><span>May</span><span>Jun</span><span>Jul</span><span>Aug</span><span>Sep</span><span>Oct</span><span>Nov</span><span>Dec</span>
  </div>
</section>

<section class="screen screen--profile">
  <div class="status-bar">
    <span>●●●○○ NOVA</span><span class="status-bar__time">4:21 PM</span>
    <span class="status-bar__battery">100% <span class="battery"></span></span>
  </div>
  <header class="app-header">
    <svg class="app-header__menu" width="12" height="11" viewBox="0 0 12 11"><rect y="0" width="12" height="2.4" fill="#3276b5"/><rect y="4.3" width="12" height="2.4" fill="#3276b5"/><rect y="8.6" width="12" height="2.4" fill="#3276b5"/></svg>
    <svg class="app-header__prev" width="5" height="8" viewBox="0 0 5 8"><path d="M4 0.5 0.8 4 4 7.5" fill="none" stroke="#fff" stroke-width="1.2"/></svg>
    <span class="app-header__title">Personal information</span>
    <svg class="app-header__next" width="5" height="8" viewBox="0 0 5 8"><path d="M1 0.5 4.2 4 1 7.5" fill="none" stroke="#fff" stroke-width="1.2"/></svg>
  </header>

  <div class="profile-name">Luca Ferrand</div>
  <div class="profile-photo" role="img" aria-label="Profile photo of the user"></div>
  <div class="profile-facts">
    <div>Age: <b>22</b>yrs</div>
    <div>Gender: <b>Male</b></div>
    <div>Height: <b>6</b>ft <b>5</b>in</div>
    <div>Weight: <b>149</b>lbs</div>
  </div>

  <div class="action-button" style="top:122px">
    <svg width="7" height="7" viewBox="0 0 7 7"><rect x="0.5" y="2.3" width="6" height="2.4" rx="1.2" transform="rotate(-40 3.5 3.5)" fill="#fff"/></svg>
    Medications<span class="action-button__more">See more</span>
  </div>
  <div class="action-button" style="top:142px">
    <svg width="7" height="7" viewBox="0 0 7 7"><rect x="1" y="1" width="5" height="6" fill="none" stroke="#fff" stroke-width=".8"/><line x1="2" y1="3" x2="5" y2="3" stroke="#fff" stroke-width=".6"/><line x1="2" y1="4.6" x2="5" y2="4.6" stroke="#fff" stroke-width=".6"/></svg>
    Consultation<span class="action-button__more">See more</span>
  </div>
  <div class="action-button" style="top:162px">
    <svg width="7" height="7" viewBox="0 0 7 7"><path d="M3.5 6.3 0.7 3.4A1.6 1.6 0 0 1 3.5 1.5 1.6 1.6 0 0 1 6.3 3.4Z" fill="#fff"/></svg>
    Health check<span class="action-button__more">See more</span>
  </div>

  <div class="section-title" style="top:183px">Friend and Family</div>
  <div class="add-profile">
    <svg width="8" height="8" viewBox="0 0 8 8"><circle cx="4" cy="4" r="4" fill="#0255a3"/><path d="M4 2v4M2 4h4" stroke="#fff" stroke-width="1"/></svg>
    Add Profile
  </div>
  <div class="list-card" style="top:198px">
    <div class="list-card__row"><span>Nora Ferrand <span class="list-card__count">(11)</span></span><span class="chevron">›</span></div>
    <div class="list-card__row"><span>Milo <span class="list-card__count">(2)</span></span><span class="chevron">›</span></div>
    <div class="list-card__row"><span>Elias Kaur <span class="list-card__count">(4)</span></span><span class="chevron">›</span></div>
  </div>

  <div class="section-title" style="top:262px">Most recently consultations</div>
  <div class="list-card" style="top:278px">
    <div class="list-card__row"><span>Depression</span><span class="chevron">›</span></div>
    <div class="list-card__row"><span>Anxiety</span><span class="chevron">›</span></div>
  </div>
</section>

<section class="screen screen--activity">
  <div class="status-bar">
    <span>●●●○○ NOVA</span><span class="status-bar__time">4:21 PM</span>
    <span class="status-bar__battery">100% <span class="battery"></span></span>
  </div>
  <header class="app-header">
    <svg class="app-header__menu" width="12" height="11" viewBox="0 0 12 11"><rect y="0" width="12" height="2.4" fill="#3276b5"/><rect y="4.3" width="12" height="2.4" fill="#3276b5"/><rect y="8.6" width="12" height="2.4" fill="#3276b5"/></svg>
    <svg class="app-header__prev" width="5" height="8" viewBox="0 0 5 8"><path d="M4 0.5 0.8 4 4 7.5" fill="none" stroke="#fff" stroke-width="1.2"/></svg>
    <span class="app-header__title app-header__title--bold">Activity</span>
    <svg class="app-header__next" width="5" height="8" viewBox="0 0 5 8"><path d="M1 0.5 4.2 4 1 7.5" fill="none" stroke="#fff" stroke-width="1.2"/></svg>
  </header>

  <div class="activity-feed">
    <article class="activity-item">
      <h2 class="activity-item__title">Physical exercises</h2>
      <p class="activity-item__body">If you want to improve your mood try gentle<br>exercises or go for a walk for 20 minutes</p>
      <p class="activity-item__date">12 Sep 2015</p>
    </article>
    <article class="activity-item">
      <h2 class="activity-item__title">Gain useful tips how to fight your bad mood</h2>
      <ul class="activity-item__body activity-item__list">
        <li>• Smile. It's cheesy, but apparently it's true: The act of smiling really can turn a frown upside down.</li>
        <li>• Jump around. Get happy-making endorphins pumping fast with some jumping jacks, jump rope, or random flailing around (hey, no judgment here) .</li>
        <li>• Chew gum. The repetitive action of gnawing on gum can promote relaxation and reduce anxiety and</li>
      </ul>
      <p class="activity-item__date">18 Sep 2015</p>
    </article>
    <article class="activity-item">
      <h2 class="activity-item__title">Test your mood regularly</h2>
      <p class="activity-item__body">Remember testing mood on a regular basis is a way to effective feedback from the app it will help you discover what makes you feel depressed and what boosts your mood.</p>
      <p class="activity-item__date">18 Sep 2015</p>
    </article>
  </div>
</section>

</body>
</html>
```